SnackOrbit!!! A Vending Machine Business Looking for an attractive website.

We are a vending machine business in Northern Michigan. We have changed our name and have rebranded our company. We would like an attractive website that shares who we are, what services we provide, the products we offer in our machines, along with a form businesses can fill out to see if they are a good fit for our company. I would like to have a Home Page, About SnackOrbit, Why Choose SnackOrbit?, Products & Services, Contact Us (With a Login Option), and a page with a questionnaire for thos interested in getting a FREE Vending Machine.

Target Market(s)

Businesses, Campgrounds, Schools, and many more in Northern Michigan

Industry/Entity Type

Vending Machines

Coding

Coded - Design and coding required

Number of Pages Required

5+ page

Requirements
Must have
• An inviting and enticing Home Page. I want to get my potential clients engaged in our website.
Nice to have
• Possibly background photos from Northern Michigan
Should not have
• A corporate feel. I do not want a boring website.

```html
<!DOCTYPE html>
<html lang="en">
<head>
<meta charset="utf-8">
<title>SnackOrbit – Crave. Vend. Repeat.</title>
<link href="https://fonts.googleapis.com/css2?family=Libre+Baskerville:wght@400;700&family=Oswald:wght@500;600&family=Josefin+Sans:wght@400;600;700&display=swap" rel="stylesheet">
<style>
:root{
  --navy:#221d54;
  --navy-deep:#1d1849;
  --green:#35582a;
  --green-dark:#2f4f25;
  --ink:#1b1b1b;
  --muted:#555;
  --white:#fff;
  --dash:#c9c9c9;
}
*{box-sizing:border-box;margin:0;padding:0}
html,body{width:1200px;height:3916px;overflow:hidden}
body{position:relative;font-family:"Josefin Sans",sans-serif;color:var(--ink);background:var(--white)}
.abs{position:absolute}
.serif{font-family:"Libre Baskerville",serif}
.btn{position:absolute;display:flex;align-items:center;justify-content:center;color:#fff;font-size:12px;font-weight:700;border-radius:4px;padding-top:2px}
.btn-navy{background:var(--navy)}
.btn-green{background:var(--green)}
.brand{font-family:"Libre Baskerville",serif;font-weight:700;color:var(--navy);display:flex;align-items:center;gap:8px;white-space:nowrap}
.brand .mark{background:var(--green)}

/* top bar */
.topbar{left:0;top:0;width:1200px;height:42px;background:var(--navy)}
.topbar .phone{left:145px;top:9px;display:flex;align-items:center;gap:8px;color:#fff;font-size:12px;font-weight:700;letter-spacing:.5px}
.ring{width:24px;height:24px;border:1.5px solid #fff;border-radius:50%;display:flex;align-items:center;justify-content:center}
.social{display:flex;gap:7px}
.social span{width:26px;height:26px;border:1.5px solid #9b98b8;border-radius:50%;display:block}
.topbar .social{left:820px;top:8px}
.login{left:960px;top:4px;width:98px;height:32px;border:1.5px solid #7fa26f;background:var(--green);border-radius:4px;color:#fff;font-size:12px;font-weight:700;display:flex;align-items:center;justify-content:center;gap:6px}

/* header */
.header{left:0;top:42px;width:1200px;height:87px;background:#fff}
.header .brand{left:155px;top:24px;font-size:32px}
.nav{left:476px;top:37px;display:flex;gap:26px;font-size:14px;color:#222}
.nav .active{color:var(--green)}
.header .btn{left:946px;top:26px;width:113px;height:38px}

/* hero */
.hero{left:0;top:129px;width:1200px;height:551px;background:linear-gradient(100deg,#f4f4f4 0%,#e8e8e8 40%,#dcdcdc 100%)}
.hero-machine{left:700px;top:140px;width:425px;height:396px;border-radius:3px;background:linear-gradient(90deg,#c21f2e 0%,#b41c2b 30%,#8e1a26 38%,#c9243a 46%,#c21f2e 62%,#b9bec4 88%,#9aa3ad 100%);box-shadow:0 18px 24px -12px rgba(0,0,0,.35)}
.hero h1{left:145px;top:195px;font-family:"Oswald",sans-serif;font-weight:600;font-size:58px;line-height:62px;color:var(--navy);letter-spacing:-.5px}
.hero h1 .g{color:var(--green)}
.hero .sub{left:145px;top:336px;font-size:22px;color:#111}
.hero .btn{left:144px;top:377px;width:123px;height:34px}

/* about */
.about-photo{left:152px;top:760px;width:415px;height:411px;border-radius:50%;background:radial-gradient(circle at 60% 45%,#e9ebed 0%,#c5c9cc 35%,#6f7a66 75%,#3f4a38 100%);border-left:8px solid var(--green);box-shadow:-2px 0 0 var(--green)}
.about .label{left:643px;top:822px;font-size:17px;font-weight:700;color:var(--green)}
.about .brand{left:637px;top:868px;font-size:36px}
.about p{left:639px;top:936px;width:420px;font-size:12px;line-height:23px;color:#222}
.about .btn{left:638px;top:1065px;width:124px;height:33px}

/* machines */
.machines{left:0;top:1249px;width:1200px;height:754px;display:flex}
.mcol{width:600px;height:100%;position:relative;color:#fff;text-align:center}
.mcol.navy{background:linear-gradient(180deg,#262062,var(--navy) 40%)}
.mcol.green{background:linear-gradient(180deg,#3b6130,var(--green) 40%)}
.mcol .pic{position:absolute;top:88px;width:205px;height:420px;border-radius:3px;box-shadow:0 10px 20px rgba(0,0,0,.35)}
.mcol.navy .pic{background:linear-gradient(180deg,#3a3a3e 0%,#8c7f86 30%,#6b6470 60%,#2c2c30 85%,#1a1a1c 100%)}
.mcol.green .pic{background:linear-gradient(180deg,#1c1e22 0%,#6e3a34 25%,#2a4a5a 55%,#7a2a2a 80%,#16181b 100%)}
.mcol h3{position:absolute;width:400px;top:518px;font-family:"Libre Baskerville",serif;font-size:26px;font-weight:700;white-space:nowrap}
.mcol p{position:absolute;width:385px;top:562px;font-size:12px;line-height:23px}
.mcol .btn{width:123px;height:34px}

/* why */
.why h2{left:0;width:1200px;top:2085px;text-align:center;font-family:"Libre Baskerville",serif;font-weight:700;font-size:38px}
.why h2 .g{color:var(--green)}.why h2 .n{color:var(--navy)}
.why .brand{left:498px;top:2336px;font-size:30px}
.feat h4{font-family:"Libre Baskerville",serif;font-size:15px;font-weight:700;line-height:21px;margin-bottom:8px;color:#111}
.feat p{font-size:11px;line-height:19px;color:#444;letter-spacing:.2px}
.feat.l{text-align:right;width:226px;left:145px}
.feat.r{width:232px;left:827px}
.icon{width:76px;height:76px;border-radius:50%;display:flex;align-items:center;justify-content:center}
.icon.n{background:var(--navy)}.icon.g{background:var(--green)}

/* testimonials */
.clients{left:0;top:2657px;width:1200px;height:498px;background:var(--green)}
.clients h2{left:0;width:1200px;top:96px;text-align:center;color:#fff;font-family:"Libre Baskerville",serif;font-size:38px;font-weight:700}
.card{top:184px;width:445px;height:160px;background:#fff;border-radius:6px}
.card::after{content:"";position:absolute;left:72px;bottom:-10px;border:10px solid transparent;border-bottom:0;border-top-color:#fff}
.card p{position:absolute;left:76px;top:42px;font-size:11.5px;line-height:22px;color:#222;white-space:nowrap}
.quote{position:absolute;font-family:"Libre Baskerville",serif;font-size:80px;line-height:80px;color:#bcb9cf}
.quote.close{left:262px;top:104px;line-height:40px;height:40px;overflow:hidden}
.person{display:flex;align-items:center;gap:12px;color:#fff;font-family:"Libre Baskerville",serif;font-size:15px;font-weight:700}
.avatar{width:52px;height:52px;border-radius:50%;border:3px solid #fff;background:linear-gradient(160deg,#c9b7a6,#8a7664)}
.arrow{width:34px;height:34px;border-radius:50%;display:flex;align-items:center;justify-content:center}

/* cta */
.cta h2{left:0;width:1200px;top:3237px;text-align:center;font-family:"Libre Baskerville",serif;font-size:38px;line-height:50px;font-weight:700}
.cta h2 .g{color:var(--green)}.cta h2 .n{color:var(--navy)}
.cta p{left:0;width:1200px;top:3355px;text-align:center;font-size:14px;line-height:26px;color:#111}
.cta .btn{left:544px;top:3419px;width:112px;height:37px}

/* footer */
.footer{left:0;top:3547px;width:1200px;height:316px;background:var(--navy);color:#fff}
.footer h5{font-family:"Libre Baskerville",serif;font-size:17px;font-weight:700}
.links{list-style:none;font-size:12px;line-height:30px}
.links li::before{content:"";display:inline-block;border:4px solid transparent;border-left:5px solid #fff;border-right:0;margin-right:8px;vertical-align:1px}
.footer .brand{color:#fff;font-size:46px}
.contact{font-size:12px;line-height:18px}
.contact .row{display:flex;gap:10px;align-items:flex-start;margin-bottom:17px}
.copy{left:0;top:3863px;width:1200px;height:53px;background:var(--green);color:#fff;text-align:center;font-family:"Libre Baskerville",serif;font-size:12px;line-height:53px}
</style>
</head>
<body>

<div class="abs topbar">
  <div class="abs phone"><span class="ring"><svg width="12" height="12" viewBox="0 0 24 24" fill="none" stroke="#fff" stroke-width="2.2"><path d="M5 3h4l2 5-3 2a11 11 0 0 0 6 6l2-3 5 2v4a2 2 0 0 1-2 2A17 17 0 0 1 3 5a2 2 0 0 1 2-2z"/></svg></span>123-456-7890</div>
  <div class="abs social"><span></span><span></span><span></span><span></span></div>
  <div class="abs login"><svg width="14" height="14" viewBox="0 0 24 24" fill="none" stroke="#fff" stroke-width="2"><circle cx="12" cy="8" r="4"/><path d="M4 21c1-5 15-5 16 0"/></svg>Login</div>
</div>

<header class="abs header">
  <div class="abs brand"><span class="mark" style="width:14px;height:14px"></span>SnackOrbit</div>
  <nav class="abs nav"><span class="active">Home</span><span>About Us</span><span>Why Choose SnackOrbit</span><span>Products &amp; Services</span></nav>
  <div class="btn btn-navy">Contact Us</div>
</header>

<section class="abs hero" role="img" aria-label="Bright white corridor with ceiling lights">
  <div class="abs hero-machine" role="img" aria-label="Row of red snack, coffee and drink vending machines"></div>
  <h1 class="abs"><span class="g">SNACKORBIT</span><br>CRAVE<span class="g">.</span> VEND<span class="g">.</span> REPEAT<span class="g">.</span></h1>
  <div class="abs sub">Elevating Snacking, One Vend at a Time</div>
  <div class="btn btn-navy">Contact Us</div>
</section>

<section class="about">
  <div class="abs about-photo" role="img" aria-label="Young woman buying a snack at a vending machine"></div>
  <div class="abs label serif">About</div>
  <div class="abs brand"><span class="mark" style="width:16px;height:16px"></span>SnackOrbit</div>
  <p class="abs">At SnackOrbit, we don't just vend snacks—we curate cravings. Our customized vending solutions bring flavor, convenience, and community to Northern Michigan. Whether you're reaching for a <b>mid-morning snack</b>, a <b>refreshing beverage</b>, or a <b>satisfying breakfast burrito</b>, SnackOrbit delivers delight with every bite</p>
  <div class="btn btn-navy">Contact Us</div>
</section>

<section class="abs machines">
  <div class="mcol navy">
    <div class="pic" style="left:268px" role="img" aria-label="Black snack vending machine stocked with chips"></div>
    <h3 style="left:171px">Vending Machine - 1</h3>
    <p style="left:178px">Lorem ipsum dolor sit amet, consectetuer adipiscing elit, sed diam nonummy nibh euismod tincidunt ut laoreet dolore magna aliquam erat volutpat. Ut wisi enim ad minim veniam.</p>
    <div class="btn btn-green" style="left:309px;top:644px">View Details</div>
  </div>
  <div class="mcol green">
    <div class="pic" style="left:126px" role="img" aria-label="Glass-front combo vending machine with snacks and drinks"></div>
    <h3 style="left:29px">Vending Machine - 2</h3>
    <p style="left:36px">Lorem ipsum dolor sit amet, consectetuer adipiscing elit, sed diam nonummy nibh euismod tincidunt ut laoreet dolore magna aliquam erat volutpat. Ut wisi enim ad minim veniam.</p>
    <div class="btn btn-navy" style="left:168px;top:645px">View Details</div>
  </div>
</section>

<section class="why">
  <h2 class="abs">Why Choose <span class="g">Snack</span><span class="n">Orbit</span></h2>
  <svg class="abs" style="left:390px;top:2152px" width="412" height="412" viewBox="0 0 412 412">
    <circle cx="206" cy="206" r="187" fill="none" stroke="var(--dash)" stroke-width="1.5" stroke-dasharray="6 6"/>
    <circle cx="206" cy="206" r="130" fill="#fff" stroke="#eee" stroke-width="3"/>
  </svg>
  <div class="abs brand"><span class="mark" style="width:14px;height:14px"></span>SnackOrbit</div>
  <div class="abs icon n" style="left:395px;top:2218px"><svg width="34" height="34" viewBox="0 0 24 24" fill="none" stroke="#fff" stroke-width="1.5"><path d="M12 21s-7-6-7-11a7 7 0 0 1 14 0c0 5-7 11-7 11z"/><path d="M12 13l-3-3a2 2 0 0 1 3-2 2 2 0 0 1 3 2z"/></svg></div>
  <div class="abs icon g" style="left:722px;top:2218px"><svg width="34" height="34" viewBox="0 0 24 24" fill="none" stroke="#fff" stroke-width="1.5"><path d="M4 20h6l5-4-2-1-3 2H7"/><circle cx="15" cy="6" r="2"/><path d="M15 8v4m-3-2h6"/></svg></div>
  <div class="abs icon g" style="left:394px;top:2421px"><svg width="34" height="34" viewBox="0 0 24 24" fill="none" stroke="#fff" stroke-width="1.5"><circle cx="12" cy="12" r="9"/><circle cx="9" cy="10" r="2"/><circle cx="15" cy="10" r="2"/><path d="M6 17c1-3 5-3 6 0m0 0c1-3 5-3 6 0"/></svg></div>
  <div class="abs icon n" style="left:722px;top:2421px"><svg width="34" height="34" viewBox="0 0 24 24" fill="none" stroke="#fff" stroke-width="1.5"><path d="M4 20h16M6 20v-5m4 5v-8m4 8v-6m4 6V9"/><path d="M5 11l5-5 4 3 5-6"/></svg></div>

  <div class="abs feat l" style="top:2193px"><h4>Local Love</h4><p>We celebrate the heart of Michigan by partnering with local legends. Say hello to Birchwood Jerky and Lakeshore Crisp Chips—our hometown heroes. Their flavorsdance on your taste buds, and we're thrilled to bring them straight to your workplace.</p></div>
  <div class="abs feat l" style="top:2401px"><h4>Unleash Your Cravings</h4><p>SnackOrbit isn't bound by corporate ties. We're the rebels of the vending world. Craving a bag of crispy, kettle-cooked chips? Done. Hankering for jerky that packs a punch? We've got you covered. Our machines are like treasure chests, waiting for you to unlock flavor magic</p></div>
  <div class="abs feat r" style="top:2193px"><h4>Quality Meets Convenience</h4><p>Imagine this: You're mid-meeting, and your stomach growls. Fear not! SnackOrbit's machines offer top-notch snacks and beverages. It's like having a mini food festival at your fingertips</p></div>
  <div class="abs feat r" style="top:2403px"><h4>Pandemic-Proof &amp;<br>Recession-Ready</h4><p>Life throws curveballs, but SnackOrbit stands strong. Our vending machines are the unsung heroes of resilience. Rain or shine, they're there, serving up joy</p></div>
</section>

<section class="abs clients">
  <h2 class="abs">What Our Clients Say</h2>
  <div class="abs arrow" style="left:85px;top:252px;border:1.5px solid #cfd8c8"><svg width="16" height="16" viewBox="0 0 24 24" fill="none" stroke="#cfd8c8" stroke-width="2.4"><path d="M20 12H5m6-6-6 6 6 6"/></svg></div>
  <div class="abs arrow" style="left:1081px;top:239px;background:var(--navy)"><svg width="16" height="16" viewBox="0 0 24 24" fill="none" stroke="#fff" stroke-width="2.4"><path d="M4 12h15m-6-6 6 6-6 6"/></svg></div>

  <div class="abs card" style="left:141px">
    <span class="quote" style="left:18px;top:10px">“</span>
    <p>Lorem ipsum dolor sit amet, consectetur adipiscing elit.<br>Maecenas pretium tortor, non consectetur nulla. Aenean<br>dignissim sit amet metus at pretium. Integer sed lectus vel<br>velit accumsan semper euac...</p>
    <span class="quote close">”</span>
  </div>
  <div class="abs person" style="left:195px;top:362px"><span class="avatar" role="img" aria-label="Client portrait"></span>Marcus Hale</div>

  <div class="abs card" style="left:614px">
    <span class="quote" style="left:18px;top:10px">“</span>
    <p>Lorem ipsum dolor sit amet, consectetur adipiscing elit.<br>Maecenas pretium tortor, non consectetur nulla. Aenean<br>dignissim sit amet metus at pretium. Integer sed lectus vel<br>velit accumsan semper euac...</p>
    <span class="quote close">”</span>
  </div>
  <div class="abs person" style="left:668px;top:362px"><span class="avatar" role="img" aria-label="Client portrait"></span>Dana Moreno</div>
</section>

<section class="cta">
  <h2 class="abs">Ready To Experience The<br><span class="g">Snack</span><span class="n">Orbit</span> Difference?</h2>
  <p class="abs">Sign up now and let's connect. Taste the future of snacking firsthand! Contact us today<br>and explore how our vending magic can elevate your space.</p>
  <div class="btn btn-green">Contact Us</div>
</section>

<footer class="abs footer">
  <h5 class="abs" style="left:144px;top:86px">Quick Links</h5>
  <ul class="abs links" style="left:144px;top:117px">
    <li>Home</li><li>About Us</li><li>Why Choose SnackOrbit</li><li>Product and Services</li><li>Contact Us</li>
  </ul>
  <div class="abs brand" style="left:430px;top:110px"><span class="mark" style="width:20px;height:20px"></span>SnackOrbit</div>
  <div class="abs social" style="left:517px;top:212px"><span style="border-color:#fff"></span><span style="border-color:#fff"></span><span style="border-color:#fff"></span><span style="border-color:#fff"></span></div>
  <h5 class="abs" style="left:868px;top:86px">Contact Details</h5>
  <div class="abs contact" style="left:868px;top:120px">
    <div class="row"><svg width="26" height="26" viewBox="0 0 24 24" fill="none" stroke="#fff" stroke-width="1.3"><circle cx="12" cy="12" r="9"/><path d="M3 12h18M12 3c3 3 3 15 0 18M12 3c-3 3-3 15 0 18"/></svg><div>123, Building Name, Street<br>City, State XY 123456</div></div>
    <div class="row"><svg width="26" height="26" viewBox="0 0 24 24" fill="none" stroke="#fff" stroke-width="1.3"><path d="M5 3h4l2 5-3 2a11 11 0 0 0 6 6l2-3 5 2v4a2 2 0 0 1-2 2A17 17 0 0 1 3 5a2 2 0 0 1 2-2z"/></svg><div>PHONE<br>123-456-7890</div></div>
    <div class="row"><svg width="26" height="26" viewBox="0 0 24 24" fill="none" stroke="#fff" stroke-width="1.3"><rect x="3" y="6" width="18" height="13" rx="1"/><path d="M3 7l9 7 9-7"/></svg><div>EMAIL<br>info@snackorbit.com</div></div>
  </div>
</footer>
<div class="abs copy">© 2024 SnackOrbit. all rights reserved.</div>

</body>
</html>
```